Laser Tattoo Removal Business Cards

We are looking for a professional business card design for a laser tattoo removal business. Ideally looking for a black business card design. The name of the business is Palewave Tattoo Removal. We place our cards at local tattoo shops so we ideally are looking for something trendy/edgy to draw both male and female clientele in.

Target Market(s)

Male/Female ages 18-60

Contact Information for Business Card

black background ideally.. hoping to stay within greys, whites and black

Font styles to use
Serif
Sans Serif

Colors
121212
a9a9a9
5c5c5c
f5f5f5
ffffff
7f7f7f
606060
848484
9d9d9d

Requirements
Must have
• Employee Info:
• Melissa Thornbury
• Chief Executive Offer
• m: 919.537.2846
• w: 919.362.4178
• f: 919.685.3907
• mthornbury@palewavetattooremoval.example
• Address:
• 4615 Oakmere Pkwy, Suite 210
• Raleigh, NC 27654
• Website:
• www.palewavetattooremoval.example
Nice to have
• Myabe business name on back or logo on back and employee info on the front

```html
<!DOCTYPE html>
<html lang="en">
<head>
<meta charset="utf-8">
<title>Palewave Tattoo Removal – Business Card</title>
<link rel="stylesheet" href="https://fonts.googleapis.com/css2?family=Roboto:wght@400;500&family=Roboto+Condensed:wght@400;700&display=swap">
<style>
  :root {
    --stage: #5c5c5c;
    --card-dark: #121212;
    --card-light: #e2e2e2;
    --card-light-edge: #d4d4d4;
    --ink: #1f1f1f;
    --ink-soft: #5c5c5c;
    --title-grey: #9d9d9d;
    --band: #262626;
    --white: #ffffff;
  }
  * { margin: 0; padding: 0; box-sizing: border-box; }
  html, body {
    width: 1200px; height: 960px; overflow: hidden;
    background: var(--stage);
    font-family: "Roboto", Arial, sans-serif;
  }
  .canvas { position: relative; width: 1200px; height: 960px; }

  .card { position: absolute; width: 600px; height: 342px; overflow: hidden; }
  .card-front { left: 322px; top: 108px; background: var(--card-light); }
  .card-back { left: 320px; top: 494px; background: var(--card-dark); }

  .card-texture {
    position: absolute; inset: 0;
    background: radial-gradient(ellipse at 40% 40%, var(--card-light) 0%, var(--card-light-edge) 100%);
  }

  .brand-front {
    position: absolute; left: 360px; top: 36px; width: 220px;
    text-align: center; color: var(--ink);
    font-family: "Roboto Condensed", Arial, sans-serif; font-weight: 700;
  }
  .brand-front .brand-name { font-size: 38px; letter-spacing: 2px; line-height: 1.1; }
  .brand-front .brand-sub { font-size: 16px; letter-spacing: 2px; margin-top: 44px; line-height: 1.2; }

  .person { position: absolute; left: 24px; top: 144px; }
  .person-name {
    font-family: "Roboto Condensed", Arial, sans-serif; font-weight: 700;
    font-size: 21px; color: var(--ink); line-height: 1.1;
  }
  .person-title { font-size: 15px; color: var(--title-grey); font-weight: 400; line-height: 1.2; }

  .contact-list { position: absolute; left: 24px; top: 193px; list-style: none; }
  .contact-list li {
    display: flex; align-items: center; height: 19px;
    font-size: 14px; color: var(--ink-soft);
  }
  .contact-list svg { width: 14px; height: 14px; margin-right: 9px; fill: var(--ink); flex: none; }

  .address-band {
    position: absolute; left: 0; top: 300px; width: 100%; height: 29px;
    background: var(--band); color: var(--white);
    display: flex; align-items: center; padding-left: 24px; font-size: 14px;
  }
  .address-band svg { width: 14px; height: 16px; margin-right: 9px; fill: var(--white); }

  .brand-back {
    position: absolute; left: 0; top: 104px; width: 100%;
    text-align: center; color: var(--white);
    font-family: "Roboto Condensed", Arial, sans-serif; font-weight: 700;
  }
  .brand-back .brand-name { font-size: 52px; letter-spacing: 3px; line-height: 1.1; }
  .brand-back .brand-sub { font-size: 21px; letter-spacing: 3px; margin-top: 62px; line-height: 1.2; }
</style>
</head>
<body>
<main class="canvas">

  <section class="card card-front">
    <div class="card-texture" role="img" aria-label="Faint light grey damask pattern across the card face"></div>

    <div class="brand-front">
      <div class="brand-name">PALEWAVE</div>
      <div class="brand-sub">TATTOO REMOVAL</div>
    </div>

    <div class="person">
      <h1 class="person-name">MELISSA THORNBURY</h1>
      <p class="person-title">Chief Executive Offer</p>
    </div>

    <ul class="contact-list">
      <li><svg viewBox="0 0 24 24"><path d="M6.6 10.8a15.1 15.1 0 0 0 6.6 6.6l2.2-2.2a1 1 0 0 1 1-.25 11.4 11.4 0 0 0 3.6.57 1 1 0 0 1 1 1V20a1 1 0 0 1-1 1A17 17 0 0 1 3 4a1 1 0 0 1 1-1h3.5a1 1 0 0 1 1 1c0 1.25.2 2.45.57 3.57a1 1 0 0 1-.25 1z"/></svg>919.362.4178</li>
      <li><svg viewBox="0 0 24 24"><path d="M7 1h10a2 2 0 0 1 2 2v18a2 2 0 0 1-2 2H7a2 2 0 0 1-2-2V3a2 2 0 0 1 2-2zm0 3v14h10V4zm5 15.5a1.2 1.2 0 1 0 0 2.4 1.2 1.2 0 0 0 0-2.4z"/></svg>919.537.2846</li>
      <li><svg viewBox="0 0 24 24"><path d="M6 2h12v5H6zM3 8h18a2 2 0 0 1 2 2v7h-4v5H5v-5H1v-7a2 2 0 0 1 2-2zm4 8v4h10v-4z"/></svg>919.685.3907</li>
      <li><svg viewBox="0 0 24 24"><path d="M2 5h20v14H2zm2 2v.5l8 5 8-5V7l-8 5z"/></svg>mthornbury@palewavetattooremoval.example</li>
      <li><svg viewBox="0 0 24 24"><circle cx="12" cy="12" r="10"/></svg>www.palewavetattooremoval.example</li>
    </ul>

    <div class="address-band">
      <svg viewBox="0 0 24 28"><path d="M12 0a10 10 0 0 0-10 10c0 7.5 10 18 10 18s10-10.5 10-18A10 10 0 0 0 12 0zm0 14a4 4 0 1 1 0-8 4 4 0 0 1 0 8z"/></svg>
      4615 Oakmere Pkwy, Suite 210, Raleigh, NC 27654
    </div>
  </section>

  <section class="card card-back">
    <div class="brand-back">
      <div class="brand-name">PALEWAVE</div>
      <div class="brand-sub">TATTOO REMOVAL</div>
    </div>
  </section>

</main>
</body>
</html>
```